Lunelle Rosa Hair Fancy Business Card’s

I want my business cards to be elite, original and very classy. I want the business cards to match the colors of my logo and to match the design posted. I would love the design of the picture I posted

I want the card all white .
The dripping on the top of the card I want it to match the pink color in my logo that’s also posted .
I need my logo on the business card !
I need my Instagram- @lunelle.rosa.hair__
And my phone number - 555 207 3962

Target Market(s)

My target market is young woman age 23 to older woman to the age of 65
I want both older and younger women to love my design . I don’t want any cheap looking business cards

Industry/Entity Type

Hair And Beauty

Contact Information for Business Card

Add my logo
Add my Instagram- @lunelle.rosa.hair__
My number - 555 207 3962
My website- www.lunellerosahair.example

Font styles to use
Serif
Script

Colors
ffffff
e667a6
e34298

Requirements
Must have
• The business cards must have my logo, my number , my website, and my Instagram!
Nice to have
• Nice to have glitter words that match my logo
• The business cards must look classy and mature
• I want them to be very unique!!
Should not have
• Should not have any colors that doesn’t match my logo ! This is very important! Please

```html
<!DOCTYPE html>
<html lang="en">
<head>
<meta charset="utf-8">
<title>Lunelle Rosa Hair – Business Card</title>
<link rel="stylesheet" href="https://fonts.googleapis.com/css2?family=Arimo:wght@400&display=swap">
<style>
  :root {
    --page-bg: #ecebea;
    --card-white: #ffffff;
    --brand-pink: #e34298;
    --soft-pink: #e667a6;
    --band-grey: #5e5a59;
    --text-light: #f4f2f2;
  }
  * { margin: 0; padding: 0; box-sizing: border-box; }
  html, body {
    width: 1200px;
    height: 900px;
    overflow: hidden;
    background: var(--page-bg);
    font-family: "Arimo", Arial, sans-serif;
  }
  .business-card {
    position: absolute;
    left: 80px;
    top: 125px;
    width: 1040px;
    height: 650px;
    background: var(--card-white);
    box-shadow: 0 10px 30px rgba(0,0,0,0.12);
    display: flex;
    flex-direction: column;
  }
  .brand-area {
    height: 404px;
    display: flex;
    align-items: center;
    justify-content: center;
    padding-top: 20px;
  }
  .brand-name {
    color: var(--brand-pink);
    font-size: 64px;
    font-weight: 400;
    letter-spacing: 2px;
  }
  .accent-rule {
    height: 10px;
    background: var(--brand-pink);
  }
  .contact-band {
    flex: 1;
    background: var(--band-grey);
    display: flex;
    justify-content: center;
    align-items: flex-end;
    padding: 0 30px 82px;
  }
  .contact-item {
    display: flex;
    flex-direction: column;
    align-items: center;
    gap: 22px;
    color: var(--text-light);
    font-size: 30px;
    line-height: 36px;
    white-space: nowrap;
  }
  .contact-divider {
    color: var(--text-light);
    font-size: 30px;
    line-height: 36px;
    padding: 0 16px;
  }
  .contact-icon {
    width: 40px;
    height: 40px;
  }
</style>
</head>
<body>
  <div class="business-card">
    <div class="brand-area">
      <div class="brand-name">Lunelle Rosa Hair</div>
    </div>
    <div class="accent-rule"></div>
    <div class="contact-band">
      <div class="contact-item">
        <svg class="contact-icon" viewBox="0 0 42 42" aria-hidden="true">
          <circle cx="21" cy="21" r="18" fill="none" stroke="var(--brand-pink)" stroke-width="2.5"/>
          <path d="M15 12 l4 0 l1.5 5 l-2.5 2 q2 4 5 5 l2 -2.5 l5 1.5 l0 4 q-1 2 -4 2 q-12 -2 -14 -14 q0 -3 3 -3z" fill="none" stroke="var(--brand-pink)" stroke-width="2" stroke-linejoin="round"/>
        </svg>
        <span class="contact-text">555 207 3962</span>
      </div>
      <span class="contact-divider">|</span>
      <div class="contact-item">
        <svg class="contact-icon" viewBox="0 0 42 42" aria-hidden="true">
          <g fill="none" stroke="var(--brand-pink)" stroke-width="2.3">
            <circle cx="21" cy="21" r="16"/>
            <ellipse cx="21" cy="21" rx="7" ry="16"/>
            <line x1="5" y1="21" x2="37" y2="21"/>
            <line x1="8" y1="13" x2="34" y2="13"/>
            <line x1="8" y1="29" x2="34" y2="29"/>
            <line x1="21" y1="5" x2="21" y2="37"/>
          </g>
        </svg>
        <span class="contact-text">www.lunellerosahair.example</span>
      </div>
      <span class="contact-divider">|</span>
      <div class="contact-item">
        <svg class="contact-icon" viewBox="0 0 42 42" aria-hidden="true">
          <circle cx="21" cy="21" r="18" fill="none" stroke="var(--brand-pink)" stroke-width="2.5"/>
          <circle cx="21" cy="21" r="4.5" fill="none" stroke="var(--brand-pink)" stroke-width="2.2"/>
          <path d="M25.5 21 v2.5 q0 3 3 3 q3.5 0 3.5 -5.5 q0 -11 -11 -11 q-11 0 -11 11 q0 11 11 11 q3.5 0 6 -1.5" fill="none" stroke="var(--brand-pink)" stroke-width="2.2" stroke-linecap="round"/>
        </svg>
        <span class="contact-text">@lunelle.rosa.hair__</span>
      </div>
    </div>
  </div>
</body>
</html>
```